New bussiness card, using company logo.
Lionel Brisk
Manager/Director
Brisk Property Developments
Po Box 5347
Tarrin Central
Nth
0491 638 205
lionel@briskpropertydevelopments
eye catching, vibrant colours, professional

```html
<!DOCTYPE html>
<html lang="en">
<head>
<meta charset="utf-8">
<title>Brisk Property Developments – Business Card</title>
<link href="https://fonts.googleapis.com/css2?family=Open+Sans:wght@400;600;700&display=swap" rel="stylesheet">
<style>
  :root {
    --page-bg: #ece7dc;
    --card-bg: #ffffff;
    --ink: #1a1a1a;
    --name-blue: #3d8ee6;
    --brand-red: #d9262e;
    --band-blue: #2d5fd4;
    --band-green: #8fd321;
    --band-cyan: #5fd8de;
  }
  * { box-sizing: border-box; margin: 0; padding: 0; }
  html, body { width: 1200px; height: 942px; overflow: hidden; }
  body {
    background: var(--page-bg);
    font-family: "Open Sans", Arial, sans-serif;
    color: var(--ink);
    position: relative;
  }
  .card {
    position: absolute;
    width: 500px;
    height: 280px;
    background: var(--card-bg);
    box-shadow: 0 6px 18px rgba(0,0,0,0.25);
    overflow: hidden;
  }
  .card-back { left: 143px; top: 189px; }
  .card-front { left: 580px; top: 490px; }
  .side-label {
    position: absolute;
    font-weight: 700;
    font-size: 24px;
  }
  .side-label.back { left: 158px; top: 486px; }
  .side-label.front { left: 884px; top: 800px; }

  .brand-mark {
    display: flex;
    align-items: center;
    gap: 8px;
    font-weight: 700;
    color: var(--brand-red);
    letter-spacing: 0.5px;
  }
  .brand-mark .dot {
    width: 14px; height: 14px;
    flex: none;
    background: var(--band-green);
  }
  .card-back .brand-mark {
    position: absolute;
    left: 0; right: 0; top: 92px;
    justify-content: center;
    font-size: 21px;
  }
  .card-back .brand-mark .dot { width: 18px; height: 18px; }
  .back-email {
    position: absolute;
    left: 0; right: 0; top: 222px;
    text-align: center;
    font-size: 17px;
    font-weight: 600;
  }

  .front-band {
    position: absolute;
    left: 0; right: 0; bottom: 0;
    height: 58px;
    background: linear-gradient(90deg, var(--band-blue) 0%, var(--band-green) 55%, var(--band-cyan) 100%);
  }
  .holder-name {
    position: absolute; left: 30px; top: 22px;
    font-size: 28px; font-weight: 600;
    color: var(--name-blue);
  }
  .holder-title {
    position: absolute; left: 30px; top: 64px;
    font-size: 15px; font-weight: 600;
  }
  .card-front .brand-mark {
    position: absolute; left: 14px; top: 116px;
    font-size: 12px;
    width: 170px;
    line-height: 1.15;
  }
  .contact-block {
    position: absolute; left: 196px; top: 104px;
    font-size: 15px; font-weight: 600;
    font-style: normal;
    line-height: 1.3;
  }
</style>
</head>
<body>
  <section class="card card-back" aria-label="Business card back">
    <div class="brand-mark"><span class="dot"></span>BRISK PROPERTY DEVELOPMENTS</div>
    <p class="back-email">lionel@briskpropertydevelopments</p>
  </section>
  <span class="side-label back">back</span>

  <section class="card card-front" aria-label="Business card front">
    <div class="front-band" role="img" aria-label="Decorative wave artwork in blue, green and cyan"></div>
    <h1 class="holder-name">Lionel Brisk</h1>
    <p class="holder-title">Manager/Director</p>
    <div class="brand-mark"><span class="dot"></span>BRISK PROPERTY<br>DEVELOPMENTS</div>
    <address class="contact-block">
      Brisk Property Developments<br>
      Po Box 5347<br>
      Tarrin Central<br>
      Nth<br>
      0491 638 205
    </address>
  </section>
  <span class="side-label front">front</span>
</body>
</html>
```